Business Card Design for Marketing Firm

Looking for business card design for higher end marketing firm. Clean but impressionable/trendy. We are a marketing firm that represents manufacturers in the foodservice equipment and supply industry. Our customers are end users such has hotels, restaurants, country clubs, convention centers and casinos as well as distributors of restaurants supplies and equipment, and manufacturers of foodservice equipment and supplies.
Target Market(s)
Hotels, Restaurants, Supply & Equipment Distributors, Foodservice Manufacturers
Industry/Entity Type
Foodservice/Hospitality
Contact Information for Business Card
Name, Title, Contact Number, Email, Website, Social Media, Address
Requirements
Must have
- Clean & Simple but Serious and Impressionable

```html
<!DOCTYPE html>
<html lang="en">
<head>
<meta charset="utf-8">
<title>Meridian Hospitality Reps — Business Card</title>
<link href="https://fonts.googleapis.com/css2?family=PT+Serif:wght@700&family=Arimo:wght@400&display=swap" rel="stylesheet">
<style>
  :root {
    --backdrop: #d3d6d6;
    --card: #fbfbfa;
    --navy: #1c1f5c;
    --ink: #55575c;
    --muted: #7a7c80;
  }
  * { box-sizing: border-box; margin: 0; padding: 0; }
  html, body { width: 1200px; height: 829px; overflow: hidden; }
  body {
    background: var(--backdrop);
    position: relative;
    font-family: "Arimo", Arial, sans-serif;
  }
  .card {
    position: absolute;
    top: 266px;
    width: 520px;
    height: 297px;
    background: var(--card);
    box-shadow: 0 6px 18px rgba(0,0,0,0.12);
    overflow: hidden;
  }
  .card--front { left: 50px; }
  .card--back { left: 630px; }

  /* Front */
  .front__bar {
    position: absolute; left: 26px; top: 30px;
    width: 12px; height: 30px; background: var(--navy);
  }
  .front__name {
    position: absolute; left: 54px; top: 30px;
    font-family: "PT Serif", Georgia, serif; font-weight: 700;
    font-size: 19px; letter-spacing: 0.5px; color: var(--navy);
  }
  .front__title {
    position: absolute; left: 54px; top: 54px;
    font-size: 11px; color: var(--muted);
  }
  .front__address {
    position: absolute; left: 54px; top: 112px;
    font-size: 11.5px; line-height: 15px; color: var(--ink);
  }
  .front__contacts {
    position: absolute; left: 40px; top: 158px;
    list-style: none; font-size: 11.5px; line-height: 17px; color: var(--ink);
  }
  .front__contacts li { display: flex; align-items: center; gap: 5px; }
  .front__contacts svg { width: 9px; height: 9px; fill: var(--navy); flex: none; }
  .front__brand {
    position: absolute; right: 34px; bottom: 64px;
    font-family: "PT Serif", Georgia, serif; font-weight: 700;
    font-size: 40px; color: var(--navy);
  }

  /* Back */
  .back__brand {
    position: absolute; left: 0; right: 0; top: 130px;
    display: flex; align-items: center; justify-content: center; gap: 10px;
    font-family: "PT Serif", Georgia, serif; font-weight: 700;
    font-size: 22px; letter-spacing: 1px; color: var(--navy);
  }
  .back__square { width: 12px; height: 12px; background: var(--navy); flex: none; }
</style>
</head>
<body>
  <section class="card card--front" aria-label="Business card front">
    <div class="front__bar"></div>
    <h1 class="front__name">DANIEL WHITMORE</h1>
    <p class="front__title">CEO/Founder</p>
    <p class="front__address">48 Harbor Lane, Suite 210<br>Lakeview, CD 51832</p>
    <ul class="front__contacts">
      <li><svg viewBox="0 0 10 10"><path d="M2 1h2l1 2-1 1c.5 1 1 1.5 2 2l1-1 2 1v2c-4 1-8-3-7-7z"/></svg>555-214-7730</li>
      <li><svg viewBox="0 0 10 10"><path d="M0 2h10v6H0z M0 2l5 3.5L10 2" stroke="#fbfbfa" stroke-width="0.8"/></svg>hello@meridianreps.com</li>
      <li><svg viewBox="0 0 10 10"><circle cx="5" cy="5" r="4.5"/></svg>www.meridianreps.com</li>
      <li><svg viewBox="0 0 10 10"><rect x="0.5" y="0.5" width="9" height="9"/></svg>@meridianreps</li>
    </ul>
    <div class="front__brand">Meridian</div>
  </section>

  <section class="card card--back" aria-label="Business card back">
    <div class="back__brand"><span class="back__square"></span>MERIDIAN HOSPITALITY REPS</div>
  </section>
</body>
</html>
```